BrimFalcon Business Cards

We have a defined brand. Please visit our website to get a feel for the product and the color pallets. www.brimfalcon-example.com

We need an updated, world class business card design. (See the attached existing card design). Please utilize BOTH sides of the card as shown and be creative with the layout. I do want the horse head icon to be positioned as it is with the existing card.

The remainder of the layout can be customized and I also want it vertically oriented.

Attached are the logo files and please use the colors as follows:
Green - #A5CE39
Tan - #CDBD99
Black

Feel free to play with the colors.

```html
<!DOCTYPE html>
<html lang="en">
<head>
<meta charset="utf-8">
<title>BrimFalcon Business Cards</title>
<link rel="stylesheet" href="https://fonts.googleapis.com/css2?family=Montserrat:wght@400;500;600&family=Barlow+Semi+Condensed:wght@700&display=swap">
<style>
  :root {
    --brand-green: #A5CE39;
    --brand-black: #111111;
    --card-white: #ffffff;
    --text-dark: #2a2a2a;
    --watermark: #ececec;
    --backdrop: #e9e9e9;
  }
  * { box-sizing: border-box; margin: 0; padding: 0; }
  html, body { width: 1200px; height: 1108px; overflow: hidden; }
  body {
    background: var(--backdrop);
    display: flex;
    align-items: center;
    justify-content: center;
    gap: 80px;
    font-family: "Montserrat", sans-serif;
  }
  .card {
    position: relative;
    width: 440px;
    height: 770px;
    border-radius: 28px;
    overflow: hidden;
    box-shadow: 0 6px 18px rgba(0,0,0,0.15);
  }

  /* Front */
  .card--front {
    background: var(--card-white);
    display: flex;
    flex-direction: column;
    align-items: center;
    text-align: center;
    color: var(--text-dark);
  }
  .front__watermark {
    position: absolute;
    width: 520px;
    height: 520px;
    border-radius: 50%;
    background: var(--watermark);
    left: -40px;
    top: 130px;
  }
  .front__content {
    position: relative;
    display: flex;
    flex-direction: column;
    align-items: center;
    padding-top: 130px;
    width: 100%;
  }
  .wordmark {
    display: flex;
    align-items: center;
    gap: 12px;
    font-weight: 600;
    font-size: 40px;
    color: var(--brand-black);
    letter-spacing: 0.5px;
  }
  .wordmark__dot {
    width: 34px; height: 34px; border-radius: 50%;
    background: var(--brand-black);
  }
  .person__name {
    margin-top: 50px;
    font-size: 33px;
    font-weight: 500;
    letter-spacing: 1px;
    color: var(--brand-black);
  }
  .person__title {
    font-size: 17px;
    font-weight: 500;
    color: var(--brand-green);
    margin-top: 2px;
  }
  .icon-row {
    display: flex;
    align-items: center;
    gap: 8px;
    margin-top: 22px;
  }
  .icon-row__rule {
    width: 60px; height: 1px; background: var(--brand-green);
  }
  .icon {
    width: 26px; height: 26px; border-radius: 50%;
    background: var(--brand-black);
    display: flex; align-items: center; justify-content: center;
  }
  .contact {
    margin-top: 14px;
    font-size: 17px;
    line-height: 1.3;
    color: var(--text-dark);
  }
  .divider {
    width: 40px; height: 1px; background: var(--brand-green);
    margin: 20px 0;
  }
  .address {
    font-size: 17px;
    line-height: 1.3;
    color: var(--text-dark);
  }

  /* Back */
  .card--back {
    background: var(--brand-green);
    display: flex;
    flex-direction: column;
    align-items: center;
  }
  .back__mark {
    margin-top: 220px;
    display: flex;
    flex-direction: column;
    align-items: center;
    gap: 24px;
  }
  .back__circle {
    width: 200px; height: 200px; border-radius: 50%;
    background: var(--brand-black);
  }
  .back__name {
    font-family: "Montserrat", sans-serif;
    font-weight: 600;
    font-size: 36px;
    color: var(--brand-black);
  }
  .tagline {
    position: absolute;
    bottom: 110px;
    width: 100%;
    text-align: center;
    font-family: "Barlow Semi Condensed", sans-serif;
    font-weight: 700;
    font-size: 34px;
    color: var(--brand-black);
  }
</style>
</head>
<body>
  <section class="card card--front">
    <div class="front__watermark" aria-hidden="true"></div>
    <div class="front__content">
      <div class="wordmark"><span class="wordmark__dot"></span>BrimFalcon</div>
      <h1 class="person__name">DANA WHITLOCK</h1>
      <p class="person__title">President &amp; CEO</p>
      <div class="icon-row">
        <span class="icon-row__rule"></span>
        <span class="icon" aria-label="phone">
          <svg width="14" height="14" viewBox="0 0 24 24"><path fill="#A5CE39" d="M6.6 10.8a15 15 0 0 0 6.6 6.6l2.2-2.2c.3-.3.7-.4 1-.2 1.1.4 2.3.6 3.6.6.6 0 1 .4 1 1V20c0 .6-.4 1-1 1A17 17 0 0 1 3 4c0-.6.4-1 1-1h3.5c.6 0 1 .4 1 1 0 1.3.2 2.5.6 3.6.1.3 0 .7-.2 1z"/></svg>
        </span>
        <span class="icon" aria-label="email">
          <svg width="14" height="14" viewBox="0 0 24 24"><rect x="3" y="6" width="18" height="12" rx="1" fill="#A5CE39"/><path d="M3 6l9 7 9-7" stroke="#111" stroke-width="1.6" fill="none"/></svg>
        </span>
        <span class="icon" aria-label="website">
          <svg width="14" height="14" viewBox="0 0 24 24"><circle cx="12" cy="12" r="9" fill="none" stroke="#A5CE39" stroke-width="2"/><path d="M3 12h18M12 3c3 3 3 15 0 18M12 3c-3 3-3 15 0 18" stroke="#A5CE39" stroke-width="1.5" fill="none"/></svg>
        </span>
        <span class="icon-row__rule"></span>
      </div>
      <p class="contact">555.014.2650<br>dana@brimfalcon-example.com<br>brimfalconlabs-example.com</p>
      <span class="divider"></span>
      <p class="address">BrimFalcon Labs LLC<br>Harrow Bay, Manitoba<br>Canada</p>
    </div>
  </section>

  <section class="card card--back">
    <div class="back__mark">
      <span class="back__circle"></span>
      <span class="back__name">BrimFalcon</span>
    </div>
    <p class="tagline">Mobility Reimagined</p>
  </section>
</body>
</html>
```